Velk Partners Building Business Cards

We need a business card that reflects our business as "Solar Experts" in San Diego. Browse our website www.velkpartners.example our License needs to be displayed as "CSLB# 3867140" our phone number is (619) 555-0187

Save thousands on your electric bills and increase the value of your home while helping to protect the environment. Our solar installation experts will help you design the system that's right for you, using only the highest quality equipment that will look great and give you ideal performance. Our goal is to make you energy independent, and get your electric bill to 0.

Paul Osterby
(619) 555-0187
paul@velkpartners.example

Target Market(s)

Home owners in san diego looking for solar

Industry/Entity Type

Solar Energy

Contact Information for Business Card

Paul Osterby
(619) 555-0187
paul@velkpartners.example

Font styles to use
Other font styles liked:
• Use our logo font

Requirements
Must have
• License needs to be displayed as "CSLB# 3867140" our phone number is (619) 555-0187
Nice to have
• Real images of rooftop home solar in san diego
Should not have
• our business address

```html
<!DOCTYPE html>
<html lang="en">
<head>
<meta charset="utf-8">
<title>Velk Partners Building – Business Cards</title>
<link rel="stylesheet" href="https://fonts.googleapis.com/css2?family=Source+Sans+3:wght@400;600;700&display=swap">
<style>
  :root {
    --backdrop: #161616;
    --card-white: #ffffff;
    --navy: #1e3a78;
    --navy-deep: #1b3a77;
    --gold: #f2a81d;
    --ink: #1f2a44;
    --rule: #9a9a9a;
  }
  * { margin: 0; padding: 0; box-sizing: border-box; }
  html, body {
    width: 1200px; height: 900px; overflow: hidden;
    background: var(--backdrop);
    font-family: "Source Sans 3", sans-serif;
  }
  .canvas { position: relative; width: 1200px; height: 900px; }
  .card {
    position: absolute; top: 306px;
    width: 440px; height: 271px;
    border-radius: 12px;
  }
  .card--front { left: 149px; background: var(--card-white); }
  .card--back { left: 608px; background: var(--navy-deep); }

  .brand {
    position: absolute; left: 0; right: 0;
    display: flex; align-items: center; justify-content: center; gap: 10px;
  }
  .card--front .brand { top: 64px; }
  .card--back .brand { top: 108px; }
  .brand__dot {
    width: 16px; height: 16px; border-radius: 50%;
    background: var(--gold);
  }
  .brand__name {
    font-weight: 700; font-size: 31px; letter-spacing: -0.3px;
    color: var(--navy);
  }
  .card--back .brand__name { color: var(--card-white); }

  .details-head {
    position: absolute; left: 31px; right: 22px; top: 168px;
    display: flex; justify-content: space-between; align-items: baseline;
  }
  .license { font-size: 13px; color: var(--ink); }
  .license__label { font-weight: 700; color: var(--navy); font-size: 14px; }
  .person { font-weight: 700; font-size: 15px; color: var(--navy); }

  .divider {
    position: absolute; left: 34px; right: 23px; top: 197px;
    height: 1px; background: var(--rule);
  }

  .contact {
    position: absolute; left: 31px; top: 207px;
    list-style: none; font-size: 12.5px; color: var(--ink); line-height: 16px;
  }
  .contact li { display: flex; align-items: center; gap: 7px; }
  .contact svg { width: 9px; height: 9px; fill: var(--navy); }
</style>
</head>
<body>
  <main class="canvas">
    <section class="card card--front">
      <div class="brand">
        <span class="brand__dot"></span>
        <span class="brand__name">Velk Partners Building</span>
      </div>
      <div class="details-head">
        <p class="license"><span class="license__label">License:</span> CSLB# 3867140</p>
        <p class="person">Paul Osterby</p>
      </div>
      <div class="divider"></div>
      <ul class="contact">
        <li>
          <svg viewBox="0 0 10 10" aria-hidden="true"><path d="M2 0.5 L3.6 0.5 L4.3 2.8 L3.2 3.7 Q4.2 5.8 6.3 6.8 L7.2 5.7 L9.5 6.4 L9.5 8 Q9.5 9.5 8 9.5 Q0.5 9 0.5 2 Q0.5 0.5 2 0.5 Z"/></svg>
          (619) 555-0187
        </li>
        <li>
          <svg viewBox="0 0 10 10" aria-hidden="true"><path d="M0.5 2 L9.5 2 L9.5 8.5 L0.5 8.5 Z M1 2.5 L5 5.6 L9 2.5" stroke="#fff" stroke-width="0.8"/></svg>
          paul@velkpartners.example
        </li>
      </ul>
    </section>

    <section class="card card--back">
      <div class="brand">
        <span class="brand__dot"></span>
        <span class="brand__name">Velk Partners Building</span>
      </div>
    </section>
  </main>
</body>
</html>
```